Career-focused learning application platform

We have a K-12 learning application platform designed for grades 6-12 that needs user interface improvements that provide a positive experience for all users (teachers and students). The learning platform provides career-focused math curriculum and career exploration resources. We would like to improve the user-interface with engaging design elements without taking away from the functionality and performance of the platform.

```html
<!DOCTYPE html>
<html lang="en">
<head>
<meta charset="utf-8">
<title>Route Ahead – Learning Platform Screens</title>
<link href="https://fonts.googleapis.com/css2?family=Roboto:wght@400;500;700;900&display=swap" rel="stylesheet">
<style>
:root{
  --purple:#4427e3;
  --purple-text:#3b22d6;
  --orange:#f47f1c;
  --ink:#1d1d1f;
  --body:#3a3a3a;
  --muted:#8b8b8b;
  --page:#f1f1f1;
  --panel:#ffffff;
  --field:#efefef;
  --line:#e3e3e3;
}
*{box-sizing:border-box;margin:0;padding:0}
html,body{width:1200px;height:3230px;overflow:hidden}
body{background:var(--page);font-family:'Roboto',sans-serif;color:var(--ink);position:relative}
.screen{position:absolute;left:82px;width:1037px;background:var(--panel);overflow:hidden}
.abs{position:absolute}
.icon{width:18px;height:18px;fill:none;stroke:currentColor;stroke-width:2;stroke-linecap:round;stroke-linejoin:round}
.topbar{position:absolute;top:0;right:0;height:48px;display:flex;align-items:center}
.topbar .bar-icon{position:absolute;top:15px}
.avatar{position:absolute;top:13px;width:22px;height:22px;border-radius:50%;background:linear-gradient(135deg,#c9a27c,#6b5a4b)}
.btn{position:absolute;display:flex;align-items:center;justify-content:center;gap:8px;color:#fff;font-weight:700;border-radius:3px;text-transform:uppercase;font-size:13px}
.btn-purple{background:var(--purple);box-shadow:0 3px 6px rgba(68,39,227,.35)}
.btn-orange{background:var(--orange);text-transform:none;font-size:13px;box-shadow:0 2px 4px rgba(244,127,28,.3)}
/* sign in */
.signin-bar{left:0;width:1037px;background:var(--purple);color:#fff}
.signin-title{left:53px;top:107px;font-size:35px;font-weight:700;line-height:37px;text-transform:uppercase}
.divider-text{left:53px;top:280px;width:311px;display:flex;align-items:center;gap:12px;font-size:13px;color:#555}
.divider-text::before,.divider-text::after{content:"";flex:1;height:1px;background:#777}
.field{left:53px;width:416px;height:38px;background:var(--field);border:1px solid #d6d6d6;display:flex;align-items:center;justify-content:space-between;padding:0 14px 0 24px;font-size:12.5px;color:#333}
.field .icon{width:14px;height:14px;color:var(--purple)}
.remember{left:53px;top:446px;font-size:13px;font-weight:500;display:flex;align-items:center;gap:10px}
.checkbox{width:16px;height:16px;border:1px solid #aaa;border-radius:3px;background:#fff}
.need{left:199px;top:446px;font-size:13px;font-weight:500}
.photo{left:522px;top:49px;width:515px;height:544px;background:linear-gradient(120deg,#6d6a68 0%,#c9c7c4 35%,#8e8a87 55%,#b0705f 80%,#5a514c 100%)}
/* app shell */
.sidebar{position:absolute;left:0;top:0;width:198px;height:100%;background:var(--purple);color:#fff}
.brand{position:absolute;left:0;top:30px;width:198px;display:flex;align-items:center;justify-content:center;gap:6px;font-size:16px;font-weight:700;color:var(--orange);letter-spacing:.5px}
.brand .dot{width:9px;height:9px;border-radius:50%;background:var(--orange)}
.nav{position:absolute;left:0;top:91px;width:198px;list-style:none}
.nav li{height:48px;display:flex;align-items:center;gap:12px;padding-left:19px;font-size:13px}
.nav li + li{margin-top:7px}
.nav li.active{background:var(--orange)}
.nav li.last{margin-top:-3px;height:48px}
.nav .icon{width:15px;height:15px;fill:#fff;stroke:none}
.appbar{position:absolute;left:198px;top:0;width:839px;height:47px;background:#fff;box-shadow:0 2px 4px rgba(0,0,0,.09);color:var(--ink)}
.main{position:absolute;left:198px;top:47px;right:0;bottom:0}
.section-title{position:absolute;font-size:25px;font-weight:700;text-transform:uppercase}
.teacher{display:flex;align-items:center;gap:8px;font-size:13px;font-weight:500}
.teacher .icon{width:12px;height:12px;fill:var(--orange);stroke:none}
.period{font-size:13px;font-weight:500;color:var(--purple-text)}
.desc{font-size:13px;color:#444}
.lesson{position:absolute;left:225px;width:784px;height:101px;background:#fff;box-shadow:0 1px 5px rgba(0,0,0,.13)}
.cover{position:absolute;width:70px;height:66px;border-radius:4px;background:linear-gradient(160deg,#1f2f52 0%,#1f2f52 40%,#f47f1c 41%,#f8a14e 100%)}
.lesson .cover{left:23px;top:17px}
.lesson h3{position:absolute;left:115px;top:21px;font-size:13.5px;font-weight:500}
.lesson p{position:absolute;left:115px;top:43px;width:500px;font-size:13.5px;line-height:22px;color:#333}
.lesson .due{position:absolute;right:22px;top:25px;font-size:13px;font-weight:700;color:var(--purple-text)}
.lesson .btn{right:33px;top:49px;width:108px;height:28px}
.assess{position:absolute;left:225px;top:774px;width:779px;height:281px;background:#fff;box-shadow:0 1px 5px rgba(0,0,0,.13);text-align:center}
.assess h2{margin-top:34px;font-size:27px;font-weight:700}
.assess p{width:660px;margin:10px auto 0;font-size:13.5px;line-height:22px;color:#333}
.assess .btn{left:321px;top:203px;width:136px;height:41px}
/* spotlight */
.tabs{left:43px;top:82px;display:flex;gap:32px;font-size:13px;font-weight:700}
.sub-title{position:absolute;font-size:25px;font-weight:700;text-transform:uppercase}
.spot-text{left:43px;top:153px;width:392px;font-size:12.5px;line-height:22.3px;color:#8a8a8a}
.earn{left:43px;top:368px;display:flex;gap:28px}
.earn div{font-size:13px;font-weight:500;line-height:26px}
.earn b{display:block;color:var(--orange);font-weight:500}
.video{left:451px;top:42px;width:300px;height:378px;background:linear-gradient(130deg,#cdd2d6 0%,#9aa1a6 40%,#d0694c 70%,#8d7d73 100%)}
.play{position:absolute;left:130px;top:169px;width:42px;height:42px;border-radius:50%;background:#fff;display:flex;align-items:center;justify-content:center}
.class-card{position:absolute;top:530px;width:202px;height:244px;background:#fff;box-shadow:0 1px 5px rgba(0,0,0,.13)}
.class-card .cover{left:22px;top:20px;width:66px;height:64px}
.class-card .cover.alg{background:linear-gradient(160deg,#4a1f4f 0%,#4a1f4f 40%,#f47f1c 41%,#f8a14e 100%)}
.class-card .info{position:absolute;left:22px;top:103px;width:170px}
.class-card .period{margin-top:6px}
.class-card .desc{margin-top:6px;line-height:19px;color:#555}
.class-card .btn{left:22px;top:192px;width:112px;height:31px;text-transform:uppercase}
.table{position:absolute;left:43px;top:901px;width:710px;height:237px;background:#fff;box-shadow:0 1px 5px rgba(0,0,0,.13);border-collapse:collapse}
.table th{height:36px;background:#f3f3f3;color:var(--orange);font-size:13.5px;font-weight:500;text-align:left}
.table td{height:42px;font-size:13.5px;color:#222;vertical-align:middle}
.table th,.table td{padding-left:76px;border-right:1px solid #e6e6e6}
.table th:nth-child(2),.table td:nth-child(2){padding-left:47px}
.table th:nth-child(3),.table td:nth-child(3){padding-left:49px;border-right:none}
.table col.c1{width:171px}.table col.c2{width:263px}
.table tr.filler td{height:auto}
</style>
</head>
<body>

<svg width="0" height="0" style="position:absolute">
  <symbol id="i-menu" viewBox="0 0 24 24"><path d="M4 6h16M4 12h16M4 18h16" stroke="currentColor" stroke-width="3" fill="none"/></symbol>
  <symbol id="i-bell" viewBox="0 0 24 24"><path d="M6 16V11a6 6 0 0 1 12 0v5l2 2H4z M10 20h4" fill="none" stroke="currentColor" stroke-width="1.8" stroke-linejoin="round"/></symbol>
  <symbol id="i-mail" viewBox="0 0 24 24"><rect x="3" y="5" width="18" height="14" rx="1.5" fill="none" stroke="currentColor" stroke-width="1.8"/><path d="M3 6l9 7 9-7" fill="none" stroke="currentColor" stroke-width="1.8"/></symbol>
  <symbol id="i-home" viewBox="0 0 24 24"><path d="M12 3l10 9h-3v9h-5v-6h-4v6H5v-9H2z"/></symbol>
  <symbol id="i-file" viewBox="0 0 24 24"><path d="M5 2h9l5 5v15H5z M8 11h8v1.5H8z M8 15h8v1.5H8z" fill-rule="evenodd"/></symbol>
  <symbol id="i-user" viewBox="0 0 24 24"><circle cx="12" cy="7" r="5"/><path d="M2 22c0-6 4-9 10-9s10 3 10 9z"/></symbol>
  <symbol id="i-userplus" viewBox="0 0 24 24"><circle cx="9" cy="7" r="5"/><path d="M0 22c0-6 3-9 9-9 3 0 5 1 6 2v7z"/><circle cx="19" cy="17" r="5"/></symbol>
  <symbol id="i-wrench" viewBox="0 0 24 24"><path d="M21 6a5 5 0 0 1-7 5L5 20a2 2 0 0 1-3-3l9-9a5 5 0 0 1 6-6l-3 3 1 3 3 1z"/></symbol>
  <symbol id="i-users" viewBox="0 0 24 24"><circle cx="12" cy="7" r="4"/><circle cx="4" cy="9" r="3"/><circle cx="20" cy="9" r="3"/><path d="M5 21c0-5 3-8 7-8s7 3 7 8z M0 19c0-4 2-6 4-6l1 6z M24 19c0-4-2-6-4-6l-1 6z"/></symbol>
  <symbol id="i-enter" viewBox="0 0 24 24"><path d="M10 6l6 6-6 6v-4H2v-4h8z M14 3h7v18h-7v-2h5V5h-5z"/></symbol>
  <symbol id="i-cog" viewBox="0 0 24 24"><circle cx="12" cy="12" r="8" fill="none" stroke="currentColor" stroke-width="2"/><circle cx="12" cy="12" r="3.5" fill="none" stroke="currentColor" stroke-width="2"/></symbol>
</svg>

<!-- Screen: sign in -->
<section class="screen" style="top:69px;height:593px">
  <header class="topbar signin-bar">
    <svg class="icon bar-icon" style="left:96px;stroke:none;color:#fff"><use href="#i-menu"/></svg>
    <svg class="icon bar-icon" style="left:834px;stroke:none;color:#fff"><use href="#i-bell"/></svg>
    <svg class="icon bar-icon" style="left:883px;stroke:none;color:#fff"><use href="#i-mail"/></svg>
    <span class="avatar" style="left:923px" role="img" aria-label="User profile photo"></span>
  </header>

  <h1 class="abs signin-title">Sign in with your<br>school account</h1>
  <div class="btn btn-purple" style="left:53px;top:204px;width:130px;height:46px;text-transform:none;font-size:14.5px"><span style="width:14px;height:14px;background:#fff;display:inline-block"></span>Northwind</div>
  <div class="btn btn-purple" style="left:198px;top:204px;width:130px;height:46px;text-transform:none;font-size:14.5px"><span style="width:14px;height:14px;border-radius:50%;background:#fff;display:inline-block"></span>Searchly</div>

  <div class="abs divider-text">or Continue With</div>
  <div class="abs field" style="top:325px">Email Address<svg class="icon"><use href="#i-mail"/></svg></div>
  <div class="abs field" style="top:377px">Password<svg class="icon" viewBox="0 0 24 24"><path d="M2 12s4-6 10-6 10 6 10 6-4 6-10 6S2 12 2 12z"/><circle cx="12" cy="12" r="3"/></svg></div>

  <div class="abs remember"><span class="checkbox"></span>Remember Me</div>
  <div class="abs need">Need An Account?</div>
  <div class="btn btn-purple" style="left:53px;top:480px;width:114px;height:39px">Sign In <svg class="icon" style="width:12px;height:12px;fill:#fff;stroke:none"><use href="#i-enter"/></svg></div>
  <div class="btn btn-purple" style="left:202px;top:480px;width:114px;height:39px">Sign In <svg class="icon" style="width:12px;height:12px;fill:#fff;stroke:none"><use href="#i-enter"/></svg></div>

  <div class="abs photo" role="img" aria-label="Photo of hands tightening a chrome sink pipe with a red pipe wrench"></div>
</section>

<!-- Screen: upcoming lessons -->
<section class="screen" style="top:717px;height:1156px">
  <aside class="sidebar">
    <div class="brand"><span class="dot"></span>ROUTE AHEAD</div>
    <ul class="nav">
      <li><svg class="icon"><use href="#i-home"/></svg>Home</li>
      <li class="active"><svg class="icon"><use href="#i-file"/></svg>Upcoming Lessons</li>
      <li><svg class="icon"><use href="#i-userplus"/></svg>Career Spotlight</li>
      <li><svg class="icon"><use href="#i-wrench"/></svg>Career Tools</li>
      <li><svg class="icon"><use href="#i-file"/></svg>Career Details</li>
      <li class="last" style="margin-top:-3px"><svg class="icon"><use href="#i-users"/></svg>Classes Assessments</li>
    </ul>
  </aside>
  <header class="appbar">
    <svg class="icon" style="position:absolute;left:33px;top:15px;color:var(--ink)"><use href="#i-menu"/></svg>
    <svg class="icon" style="position:absolute;left:636px;top:15px"><use href="#i-bell"/></svg>
    <svg class="icon" style="position:absolute;left:685px;top:15px"><use href="#i-mail"/></svg>
    <span class="avatar" style="left:725px" role="img" aria-label="User profile photo"></span>
  </header>

  <div class="abs" style="left:226px;top:79px">
    <div class="teacher"><svg class="icon"><use href="#i-user"/></svg>Math Teacher</div>
    <div class="period" style="margin-top:5px">Period 1</div>
    <div class="desc" style="margin-top:5px">Lorem ipsum dolor sit amet, consectetur</div>
  </div>
  <div class="btn btn-purple" style="left:606px;top:88px;width:148px;height:44px;font-size:13px"><svg class="icon" style="width:11px;height:11px;fill:#fff;stroke:none"><use href="#i-user"/></svg>Class Roster</div>
  <div class="btn btn-purple" style="left:769px;top:88px;width:148px;height:44px;font-size:13px"><svg class="icon" style="width:13px;height:13px;color:#fff;stroke:none"><use href="#i-cog"/></svg>Class Settings</div>

  <h2 class="section-title" style="left:224px;top:164px">Upcoming Lessons</h2>

  <article class="lesson" style="top:210px"><div class="cover" role="img" aria-label="Grade 6 math course book cover"></div><h3>1:1 Translations</h3><p>Lorem ipsum dolor sit amet, consectetur adipiscing elit, sed do eiusmod tempor incididunt ut labore et dolore magna aliqua. Ut enim ad minim veniam quis nostrud.</p><span class="due">Due 10/15at 11:59pm</span><span class="btn btn-orange">Begin Lesson</span></article>
  <article class="lesson" style="top:323px"><div class="cover" role="img" aria-label="Grade 6 math course book cover"></div><h3>1:2 Translations</h3><p>Lorem ipsum dolor sit amet, consectetur adipiscing elit, sed do eiusmod tempor incididunt ut labore et dolore magna aliqua. Ut enim ad minim veniam quis nostrud.</p><span class="due">Due 10/15at 11:59pm</span><span class="btn btn-orange">Begin Lesson</span></article>
  <article class="lesson" style="top:436px"><div class="cover" role="img" aria-label="Grade 6 math course book cover"></div><h3>1:2 Translations</h3><p>Lorem ipsum dolor sit amet, consectetur adipiscing elit, sed do eiusmod tempor incididunt ut labore et dolore magna aliqua. Ut enim ad minim veniam quis nostrud.</p><span class="due">Due 10/15at 11:59pm</span><span class="btn btn-orange">Begin Lesson</span></article>
  <article class="lesson" style="top:549px"><div class="cover" role="img" aria-label="Grade 6 math course book cover"></div><h3>1:2 Translations</h3><p>Lorem ipsum dolor sit amet, consectetur adipiscing elit, sed do eiusmod tempor incididunt ut labore et dolore magna aliqua. Ut enim ad minim veniam quis nostrud.</p><span class="due">Due 10/15at 11:59pm</span><span class="btn btn-orange">Begin Lesson</span></article>
  <article class="lesson" style="top:662px"><div class="cover" role="img" aria-label="Grade 6 math course book cover"></div><h3>1:2 Translations</h3><p>Lorem ipsum dolor sit amet, consectetur adipiscing elit, sed do eiusmod tempor incididunt ut labore et dolore magna aliqua. Ut enim ad minim veniam quis nostrud.</p><span class="due">Due 10/15at 11:59pm</span><span class="btn btn-orange">Begin Lesson</span></article>

  <section class="assess">
    <h2>RTA ASSESSMENTS</h2>
    <p>Lorem ipsum dolor sit amet, consectetur adipiscing elit, sed do eiusmod tempor incididunt ut labore et dolore magna aliqua. Ut enim ad minim veniam, quis nostrud exercitation ullamco laboris nisi ut aliquip ex ea commodo consequat. Duis aute irure dolor in reprehenderit in voluptate velit esse cillum dolore eu fugiat nulla pariaturperspiciatis unde omnis iste natus error sit voluptatem accusantium doloremque laudantium, totam rem aperiam, eaque ipsa quae ab illo inventore veritatis et quasi architecto beatae vitae dicta</p>
    <span class="btn btn-purple">Go There Now</span>
  </section>
</section>

<!-- Screen: career spotlight -->
<section class="screen" style="top:1927px;height:1233px">
  <aside class="sidebar">
    <div class="brand"><span class="dot"></span>ROUTE AHEAD</div>
    <ul class="nav">
      <li><svg class="icon"><use href="#i-home"/></svg>Home</li>
      <li><svg class="icon"><use href="#i-file"/></svg>Upcoming Lessons</li>
      <li class="active"><svg class="icon"><use href="#i-userplus"/></svg>Career Spotlight</li>
      <li><svg class="icon"><use href="#i-wrench"/></svg>Career Tools</li>
      <li><svg class="icon"><use href="#i-file"/></svg>Career Details</li>
      <li class="last" style="margin-top:-3px"><svg class="icon"><use href="#i-users"/></svg>Classes Assessments</li>
    </ul>
  </aside>
  <header class="appbar">
    <svg class="icon" style="position:absolute;left:33px;top:15px"><use href="#i-menu"/></svg>
    <svg class="icon" style="position:absolute;left:636px;top:15px"><use href="#i-bell"/></svg>
    <svg class="icon" style="position:absolute;left:685px;top:15px"><use href="#i-mail"/></svg>
    <span class="avatar" style="left:725px" role="img" aria-label="User profile photo"></span>
  </header>

  <div class="main">
    <h2 class="sub-title" style="left:43px;top:37px">Career Spotlight</h2>
    <div class="abs tabs"><span>PLUMBERS</span><span>PIPERFITTERS</span><span>STEAMFITTERS</span></div>
    <h2 class="sub-title" style="left:43px;top:112px">What They Do</h2>
    <p class="abs spot-text">Lorem ipsum dolor sit amet, consectetur adipiscing elit, sed do eiusmod tempor incididunt ut labore et dolore magna aliqua. Ut enim ad minim veniam, quis nostrud exercitation ullamco laboris nisi ut aliquip ex ea commodo consequat. Duis aute irure dolor in reprehenderit in voluptate velit esse cillum dolore eu fugiat nulla pariatur. Excepteur sint occaecat cupidatat non proident, sunt in culpa qui officia deserunt mollit anim id est</p>
    <h2 class="sub-title" style="left:43px;top:323px">Earnings</h2>
    <div class="abs earn">
      <div>LOW END<b>$33,460</b></div>
      <div>MEDIAN<b>$33,460</b></div>
      <div>HIGH END<b>$33,460</b></div>
    </div>
    <div class="abs video" role="img" aria-label="Video still of a plumber fitting a chrome pipe under a sink">
      <span class="play"><svg width="16" height="18" viewBox="0 0 16 18"><path d="M2 1l13 8-13 8z" fill="#222"/></svg></span>
    </div>

    <h2 class="sub-title" style="left:43px;top:478px">Classes</h2>
    <article class="class-card" style="left:43px">
      <div class="cover" role="img" aria-label="Grade 6 math course book cover"></div>
      <div class="info"><div class="teacher"><svg class="icon"><use href="#i-user"/></svg>Math Teacher</div><div class="period">Period 1</div><div class="desc">Lorem ipsum dolor amet consectetur adipiscing sed</div></div>
      <span class="btn btn-orange">Go to class</span>
    </article>
    <article class="class-card" style="left:266px">
      <div class="cover alg" role="img" aria-label="Algebra I course book cover"></div>
      <div class="info" style="top:106px"><div class="teacher"><svg class="icon"><use href="#i-user"/></svg>Math Teacher</div><div class="period">Period 6</div><div class="desc">Lorem ipsum dolor amet consectetur adipiscing sed</div></div>
      <span class="btn btn-orange" style="top:195px">Go to class</span>
    </article>
    <article class="class-card" style="left:488px">
      <div class="cover alg" role="img" aria-label="Algebra I course book cover"></div>
      <div class="info"><div class="teacher"><svg class="icon"><use href="#i-user"/></svg>Math Teacher</div><div class="period">Period 5</div><div class="desc">Lorem ipsum dolor amet consectetur adipiscing sed</div></div>
      <span class="btn btn-orange">Go to class</span>
    </article>

    <h2 class="sub-title" style="left:43px;top:833px">Upcoming Lessons</h2>
    <p class="abs desc" style="left:43px;top:869px">Lorem ipsum dolor sit amet, consectetur</p>
    <table class="table">
      <colgroup><col class="c1"><col class="c2"><col></colgroup>
      <thead><tr><th>CLASS</th><th>LESSON</th><th>DUE</th></tr></thead>
      <tbody>
        <tr><td>Period 1</td><td>Lorem ipsum dolor sit amet</td><td>October 15 th at 11:59Pm</td></tr>
        <tr><td>Period 1</td><td>Lorem ipsum dolor sit amet</td><td>October 15 th at 11:59Pm</td></tr>
        <tr><td>Period 1</td><td>Lorem ipsum dolor sit amet</td><td>October 15 th at 11:59Pm</td></tr>
        <tr><td>Period 1</td><td>Lorem ipsum dolor sit amet</td><td>October 15 th at 11:59Pm</td></tr>
        <tr class="filler"><td></td><td></td><td></td></tr>
      </tbody>
    </table>
  </div>
</section>

</body>
</html>
```